Need a book cover design for book titled: Crossing the Quiet River--Simple Practices for Daily Calm

This book describes and presents tools to connect with and activate the Lightbody that we all carry within us. It talks about the Lighbody, brief history, lightbody levels and offers exercises to bring light into the body.
I envision a design that shows a physical body changing into light /surrounded by light; a resurrected body ascending to higher dimensions of Spirit o anything comparable .

Need extra days to review

Need extra days to review

Mature audience of spiritual seekers and those on spiritual path

• Space on backcover for book summary at top and title and author name on spine.

```html
<!DOCTYPE html>
<html lang="en">
<head>
<meta charset="utf-8">
<title>Crossing the Quiet River — Book Cover</title>
<link rel="stylesheet" href="https://fonts.googleapis.com/css2?family=Cinzel+Decorative:wght@700&family=Cinzel:wght@400;600&family=Marcellus&display=swap">
<style>
  :root {
    --night: #050506;
    --ember: #c8641a;
    --amber: #f0a23a;
    --rust: #6a2408;
    --glow-white: #fffaf2;
    --sky-blue: #2f9fd0;
    --deep-blue: #1f4f80;
    --silver-light: #f4f4f4;
    --silver-mid: #b9b9b9;
    --silver-dark: #7d7d7d;
    --halo-blue: rgba(90, 160, 255, 0.85);
  }
  * { margin: 0; padding: 0; box-sizing: border-box; }
  html, body {
    width: 800px; height: 1200px; overflow: hidden; background: var(--night);
  }
  .cover {
    position: relative; width: 800px; height: 1200px; overflow: hidden;
    background: var(--night);
  }
  .cover-art {
    position: absolute; inset: 0;
    background:
      linear-gradient(to bottom, rgba(5,5,6,0) 0%, rgba(5,5,6,0) 55%, rgba(5,5,6,0.75) 75%, var(--night) 92%),
      radial-gradient(ellipse 150px 200px at 50% 22%, var(--glow-white) 0%, rgba(255,250,242,0.9) 45%, rgba(255,250,242,0) 100%),
      radial-gradient(ellipse 180px 200px at 52% 48%, var(--sky-blue) 0%, var(--deep-blue) 55%, rgba(31,79,128,0) 100%),
      radial-gradient(ellipse 60px 80px at 52% 61%, rgba(255,255,255,0.95) 0%, rgba(200,220,255,0.4) 50%, rgba(255,255,255,0) 100%),
      radial-gradient(ellipse 380px 520px at 50% 30%, var(--amber) 0%, var(--ember) 55%, var(--rust) 80%, rgba(20,6,2,1) 100%);
  }
  .title-block {
    position: absolute; left: 0; top: 0; width: 800px; height: 1200px;
  }
  .silver {
    background: linear-gradient(to bottom, var(--silver-light) 0%, var(--silver-mid) 45%, var(--silver-light) 60%, var(--silver-dark) 100%);
    -webkit-background-clip: text; background-clip: text; color: transparent;
    filter: drop-shadow(0 2px 3px rgba(0,0,0,0.8));
  }
  .title-main {
    position: absolute; left: 0; width: 800px; text-align: center;
    font-family: "Cinzel Decorative", "Cinzel", serif; font-weight: 700;
  }
  .title-first { top: 722px; font-size: 104px; letter-spacing: 1px; }
  .title-connector {
    position: absolute; left: 118px; top: 888px;
    font-family: "Cinzel", serif; font-weight: 400; font-size: 38px;
    color: var(--silver-light);
  }
  .title-last {
    position: absolute; left: 345px; top: 842px;
    font-family: "Cinzel", serif; font-weight: 600; font-size: 118px;
    letter-spacing: 2px;
  }
  .title-last-glow {
    position: absolute; left: 345px; top: 842px;
    font-family: "Cinzel", serif; font-weight: 600; font-size: 118px;
    letter-spacing: 2px; color: transparent;
    text-shadow: 0 0 18px var(--halo-blue), 0 0 36px rgba(60,120,230,0.6);
  }
  .subtitle {
    position: absolute; left: 0; width: 800px; text-align: center;
    font-family: "Cinzel", serif; font-weight: 400; font-size: 42px;
    color: var(--silver-light); line-height: 64px; top: 990px;
    text-shadow: 0 2px 3px rgba(0,0,0,0.8);
  }
  .author {
    position: absolute; left: 0; width: 800px; text-align: center; top: 1140px;
    font-family: "Marcellus", serif; font-size: 38px; color: var(--silver-mid);
    letter-spacing: 1px;
  }
</style>
</head>
<body>
  <main class="cover">
    <div class="cover-art" role="img" aria-label="Glowing figure of light walking across a wooden bridge toward a bright opening in a fiery orange tunnel of branches, blue sky and clouds beyond"></div>
    <h1 class="title-block">
      <span class="title-main title-first silver">CROSSING</span>
      <span class="title-connector">THE QUIET</span>
      <span class="title-last-glow" aria-hidden="true">RIVER</span>
      <span class="title-last silver">RIVER</span>
    </h1>
    <p class="subtitle">SIMPLE PRACTICES FOR<br>DAILY CALM</p>
    <p class="author">Daniel R. Serrano PhD</p>
  </main>
</body>
</html>
```